Professional Photography Business cards

I need business cards that include my logo which I have uploaded. I run a photography business. I am open to ideas but I would like one side to have my logo and the other side to have my contact info. I don't have a website made but I do own a website domain. I have uploaded 2 different logo color schemes. My business colors are Blue, black , and white.

Business Name
Business Phone Number
Business Email
Business Website address
Instagram

Industry/Entity Type

Professional Photography

Contact Information for Business Card

Phone Number: 916-384-7702 email: info@tlane-studio.example Instagram: @t.lanestudio website doman- www.tlane-studio.example

Requirements
Must have
• I like the idea of a business card with a full black background front and back of card. My colors must include royal blue, black, and white

```html
<!DOCTYPE html>
<html lang="en">
<head>
<meta charset="utf-8">
<title>T. Lane Studio — Business Cards</title>
<link rel="stylesheet" href="https://fonts.googleapis.com/css2?family=Arimo:wght@400&display=swap">
<style>
  :root {
    --stage: #a3a3a3;
    --royal-blue: #0a0f9e;
    --ink-black: #000000;
    --paper-white: #ffffff;
    --text-dark: #1a1a1a;
    --rule-grey: #8c8c8c;
  }
  * { box-sizing: border-box; margin: 0; padding: 0; }
  html, body {
    width: 1200px;
    height: 1200px;
    overflow: hidden;
    background: var(--stage);
    font-family: "Arimo", Arial, sans-serif;
  }
  .card {
    position: absolute;
    top: 303px;
    width: 369px;
    height: 594px;
    overflow: hidden;
  }
  /* Front */
  .card-front {
    left: 200px;
    background: var(--ink-black);
  }
  .front-field {
    position: absolute;
    left: 0; top: 0;
    width: 369px;
    height: 594px;
  }
  .front-brand {
    position: absolute;
    left: 44px;
    top: 496px;
    display: flex;
    align-items: center;
    gap: 12px;
  }
  .front-brand .brand-dot {
    width: 16px; height: 16px;
    border-radius: 50%;
    background: var(--paper-white);
  }
  .front-brand .brand-name {
    color: var(--paper-white);
    font-size: 30px;
    letter-spacing: 1px;
    white-space: nowrap;
  }
  /* Back */
  .card-back {
    left: 599px;
    width: 364px;
    background: var(--paper-white);
  }
  .back-brand {
    position: absolute;
    left: 0; right: 0;
    top: 150px;
    display: flex;
    justify-content: center;
    align-items: center;
    gap: 12px;
  }
  .back-brand .brand-dot {
    width: 16px; height: 16px;
    border-radius: 50%;
    background: var(--royal-blue);
  }
  .back-brand .brand-name {
    color: var(--royal-blue);
    font-size: 30px;
    letter-spacing: 1px;
    white-space: nowrap;
  }
  .icon-row, .social-row {
    position: absolute;
    left: 0; right: 0;
    display: flex;
    justify-content: center;
    align-items: center;
    gap: 4px;
  }
  .icon-row { top: 388px; }
  .social-row { top: 499px; }
  .rule {
    width: 66px;
    height: 1px;
    background: var(--rule-grey);
    margin: 0 4px;
  }
  .contact-icon {
    width: 25px; height: 25px;
    border-radius: 3px;
    background: var(--royal-blue);
    display: flex;
    align-items: center;
    justify-content: center;
  }
  .social-dot {
    width: 26px; height: 26px;
    border-radius: 50%;
    background: var(--royal-blue);
    margin: 0 2px;
  }
  .contact-lines {
    position: absolute;
    left: 0; right: 0;
    top: 423px;
    text-align: center;
    color: var(--text-dark);
    font-size: 16px;
    line-height: 21.5px;
  }
  .social-handle {
    position: absolute;
    left: 0; right: 0;
    top: 534px;
    text-align: center;
    color: var(--text-dark);
    font-size: 16px;
  }
</style>
</head>
<body>
  <section class="card card-front">
    <svg class="front-field" viewBox="0 0 369 594" role="img" aria-label="Royal blue emblem field rising into the black top band">
      <path d="M0 225 C 70 224, 80 168, 160 163 C 240 158, 270 200, 330 206 C 360 210, 369 230, 369 250 L369 594 L0 594 Z" fill="var(--royal-blue)"/>
    </svg>
    <div class="front-brand">
      <span class="brand-dot"></span>
      <span class="brand-name">T. Lane Studio</span>
    </div>
  </section>

  <section class="card card-back">
    <div class="back-brand">
      <span class="brand-name">T. Lane Studio</span>
      <span class="brand-dot"></span>
    </div>

    <div class="icon-row">
      <span class="rule"></span>
      <span class="contact-icon" aria-label="Phone">
        <svg width="15" height="15" viewBox="0 0 24 24" fill="#fff"><path d="M6.6 10.8a15.1 15.1 0 0 0 6.6 6.6l2.2-2.2c.3-.3.7-.4 1-.2 1.1.4 2.3.6 3.6.6.6 0 1 .4 1 1V20c0 .6-.4 1-1 1A17 17 0 0 1 3 4c0-.6.4-1 1-1h3.5c.6 0 1 .4 1 1 0 1.3.2 2.5.6 3.6.1.3 0 .7-.2 1z"/></svg>
      </span>
      <span class="contact-icon" aria-label="Email">
        <svg width="15" height="15" viewBox="0 0 24 24" fill="none" stroke="#fff" stroke-width="2"><rect x="3" y="5" width="18" height="14"/><path d="M3 5l9 8 9-8M3 19l7-7M21 19l-7-7"/></svg>
      </span>
      <span class="contact-icon" aria-label="Website">
        <svg width="15" height="15" viewBox="0 0 24 24" fill="none" stroke="#fff" stroke-width="2"><circle cx="12" cy="12" r="9"/><path d="M3 12h18M12 3c3 3 3 15 0 18M12 3c-3 3-3 15 0 18"/></svg>
      </span>
      <span class="rule"></span>
    </div>

    <div class="contact-lines">
      <p class="contact-phone">916-384-7702</p>
      <p class="contact-email">info@tlane-studio.example</p>
      <p class="contact-web">www.tlane-studio.example</p>
    </div>

    <div class="social-row">
      <span class="rule"></span>
      <span class="social-dot"></span>
      <span class="rule"></span>
    </div>
    <p class="social-handle">@t.lanestudio</p>
  </section>
</body>
</html>
```